Software Product Flyer Design

A established czech software company needs a marketing flyer to promote their software product and its modules.
The overall feel of the flyer must to be serious, but also eye-catching, enticing, clever and bold to attract customers.
Unifying graphic element is the new product logo.
The flyer would be A4, colour both sides and folded once (to give 4 pages of A5).
Title page - product logo with module name and module icon, short presentation of the product and list of its key features.
Inside pages - detailed informations with screenshots or graphical schemas.
Back side - informations about technical requirements and user support, contacts (address, phone, fax, e-mail, web pages - no social networks).
Product logo, module icon and some images attached.
Updates
Hello,
Reason: For organizational reasons we extending the deadline by 10 days.
FYI: We have uploaded the new ZIP file with previous version of our flyer.
Attached PDF file with text for inner pages.
Target Market(s)
Existing or new customers like municipalities, public authorities and nonprofit organizations.
Industry/Entity Type
Marketing
Requirements
Must have
- Winning designer must provide a template for Adobe InDesign based on his graphic design.
Avoid to using exotic fonts - in Czech we use Latin Extended characters (like áéěíýůčřžšťďň).
Nice to have
- Using graphic motif from product logo like as attached splash screen.

```html
<!DOCTYPE html>
<html lang="en">
<head>
<meta charset="utf-8">
<title>Velora – Software Product Flyer</title>
<link rel="stylesheet" href="https://fonts.googleapis.com/css2?family=Questrial&family=Source+Sans+3:ital,wght@1,400&display=swap">
<style>
  :root {
    --orange: #f15c22;
    --orange-deep: #e2521b;
    --orange-tint: rgba(255, 255, 255, 0.06);
    --orange-shade: rgba(120, 40, 10, 0.22);
    --silver-light: #e4e5e6;
    --silver-mid: #b9bbbd;
    --silver-dark: #8d9093;
    --silver-tint: rgba(255, 255, 255, 0.16);
    --ink: #3d4349;
    --white: #ffffff;
    --icon-light: #dfe9f6;
    --icon-mid: #b7cde9;
  }
  * { margin: 0; padding: 0; box-sizing: border-box; }
  html, body {
    width: 1200px;
    height: 896px;
    overflow: hidden;
    background: var(--silver-light);
  }
  .flyer-spread {
    position: relative;
    width: 1200px;
    height: 896px;
    display: flex;
  }

  /* Rounded-square motif */
  .motif {
    position: absolute;
    border-radius: 22%;
  }
  .motif--tint-orange {
    background: var(--orange-tint);
    box-shadow: 0 6px 18px rgba(120, 40, 10, 0.10);
  }
  .motif--solid-orange {
    background: var(--orange);
    box-shadow: 0 4px 10px var(--orange-shade);
  }
  .motif--tint-silver {
    background: var(--silver-tint);
  }

  /* Back page */
  .back-page {
    position: relative;
    width: 600px;
    height: 896px;
    overflow: hidden;
    background: linear-gradient(160deg, var(--orange) 0%, var(--orange-deep) 100%);
  }
  .back-brand {
    position: absolute;
    left: 311px;
    top: 684px;
    display: flex;
    align-items: center;
    gap: 10px;
    font-family: "Questrial", sans-serif;
    font-size: 40px;
    line-height: 1;
    color: var(--white);
  }
  .back-brand .brand-square {
    width: 22px;
    height: 22px;
    background: var(--white);
    border-radius: 5px;
  }
  .contact-block {
    position: absolute;
    left: 311px;
    top: 746px;
    font-family: "Source Sans 3", sans-serif;
    font-style: italic;
    font-size: 14px;
    color: var(--white);
    line-height: 20px;
  }
  .contact-block .contact-address { margin-top: 6px; }
  .contact-block .contact-web {
    margin-top: 12px;
    letter-spacing: 1.5px;
  }

  /* Title page */
  .title-page {
    position: relative;
    width: 600px;
    height: 896px;
    overflow: hidden;
    background: radial-gradient(ellipse 70% 45% at 55% 25%, var(--silver-light) 0%, var(--silver-mid) 60%, var(--silver-dark) 100%);
  }
  .product-name {
    position: absolute;
    left: 0;
    top: 92px;
    width: 600px;
    text-align: center;
    font-family: "Questrial", sans-serif;
    font-size: 104px;
    line-height: 1;
    color: var(--ink);
    letter-spacing: -1px;
  }
  .product-tagline {
    position: absolute;
    left: 0;
    top: 214px;
    width: 600px;
    text-align: center;
    font-family: "Questrial", sans-serif;
    font-size: 16px;
    letter-spacing: 1.6px;
    color: var(--ink);
  }
  .module-icon {
    position: absolute;
    left: 160px;
    top: 513px;
  }
  .title-web {
    position: absolute;
    left: 0;
    top: 842px;
    width: 600px;
    text-align: center;
    font-family: "Source Sans 3", sans-serif;
    font-style: italic;
    font-size: 15px;
    letter-spacing: 6px;
    color: var(--white);
  }
</style>
</head>
<body>
  <main class="flyer-spread">
    <section class="back-page">
      <div class="motif motif--tint-orange" style="left:70px; top:82px; width:300px; height:296px;"></div>
      <div class="motif motif--tint-orange" style="left:292px; top:4px; width:310px; height:302px;"></div>
      <div class="motif motif--tint-orange" style="left:292px; top:226px; width:304px; height:304px;"></div>
      <div class="motif motif--solid-orange" style="left:230px; top:556px; width:88px; height:92px;"></div>
      <div class="motif motif--solid-orange" style="left:4px; top:608px; width:178px; height:188px;"></div>

      <div class="back-brand">
        <span class="brand-square"></span>
        <span class="brand-name">velora</span>
      </div>
      <address class="contact-block">
        <p class="contact-phone">P : 0123.456.789</p>
        <p class="contact-fax">F : 0123.456.789</p>
        <p class="contact-email">E : info@velora-soft.com</p>
        <p class="contact-address">Suite300, Cityname, Countryname 0000.</p>
        <p class="contact-web">www.velora-soft.com</p>
      </address>
    </section>

    <section class="title-page">
      <div class="motif motif--tint-silver" style="left:31px; top:336px; width:308px; height:316px; transform:rotate(12deg);"></div>
      <div class="motif motif--tint-silver" style="left:424px; top:366px; width:150px; height:158px; transform:rotate(12deg);"></div>

      <h1 class="product-name">velora</h1>
      <p class="product-tagline">A Established Czech Software Company</p>
      <svg class="module-icon" width="274" height="277" viewBox="0 0 274 277" role="img" aria-label="Module icon: address book with letter A">
        <defs>
          <linearGradient id="module-icon-fill" x1="0" y1="0" x2="0" y2="1">
            <stop offset="0" stop-color="#dfe9f6"/>
            <stop offset="1" stop-color="#b7cde9"/>
          </linearGradient>
        </defs>
        <rect x="20" y="2" width="222" height="270" rx="8" fill="url(#module-icon-fill)"/>
      </svg>
      <p class="title-web">www.velora-soft.com</p>
    </section>
  </main>
</body>
</html>
```